Dietitian needs awesome business card

I need a contemporary design that's eye catching but professional.
My card is to given to doctors, specialists and patients alike.
I manage patients with chronic diseases
I have uploaded my logo and current business card, I would also like the other Certified Clinical Nutritionist logo incorporated into the design

Target Market(s)

Doctors, specialists and patients

Industry/Entity Type

Healthcare

Contact Information for Business Card

www.brightfieldnutrition.com.au
Ph: 0427 561 903
Fax: 6457 2183
email: marcus.k.diet@fernmail.com
Space on the back of the card with: Appointment date, Appointment time and appointment location

Font styles to use
Serif

Colors
fbee3e
876aae
ffc214

Requirements
Must have
• My Logo
• Certified Clinical Nutritionist Logo
• My 4 locations - Pinebrook Medical Centre, North Corrin Health, Hollis Medical, Ashcombe Doctors Surgery
Nice to have
• I like the colours in my current business card

```html
<!DOCTYPE html>
<html lang="en">
<head>
<meta charset="utf-8">
<title>Brightfield Nutrition &amp; Dietetics – Business Card</title>
<link href="https://fonts.googleapis.com/css2?family=Cinzel:wght@600;700&family=Marcellus&display=swap" rel="stylesheet">
<style>
  :root{
    --backdrop:#e9e6e1;
    --card-dark:#2a2c2d;
    --card-darker:#1b1c1d;
    --paper:#ffffff;
    --paper-shade:#eceeef;
    --band-green:#27b24a;
    --band-lime:#d6e21f;
    --brand-blue:#2a9fd6;
    --rule-blue:#2a7fd6;
    --ink:#1f1f1f;
    --ink-soft:#555;
    --badge-orange:#f7a21b;
    --icon-lime:#c8dc2a;
    --text-light:#f4f4f4;
  }
  *{margin:0;padding:0;box-sizing:border-box}
  html,body{width:1200px;height:1023px;overflow:hidden}
  body{background:var(--backdrop);position:relative;font-family:"Marcellus",serif}
  .card{position:absolute;top:200px;width:380px;height:620px;border-radius:22px;overflow:hidden;
        box-shadow:0 14px 30px rgba(0,0,0,.25)}
  .card--back{left:170px;background:linear-gradient(180deg,var(--card-dark),var(--card-darker))}
  .card--front{left:650px;background:linear-gradient(180deg,var(--card-dark),var(--card-darker))}

  .brand-name{position:absolute;right:30px;top:36px;width:200px;text-align:right;
              font-family:"Marcellus",serif;font-weight:400;font-size:20px;line-height:1.25}
  .card--back .brand-name{color:var(--brand-blue)}
  .card--front .brand-name{color:var(--band-lime)}

  .appt-sheet{position:absolute;left:0;top:0;width:100%;height:300px;
              background:linear-gradient(180deg,var(--paper),var(--paper-shade));
              border-bottom:2px solid var(--rule-blue)}
  .appt-fields{position:absolute;left:30px;right:30px;top:128px;list-style:none}
  .appt-field{display:flex;align-items:flex-end;font-size:17px;color:var(--ink-soft);height:38px}
  .appt-field__line{flex:1;border-bottom:2px dotted #777;margin-left:8px;margin-bottom:5px}

  .band{position:absolute;left:0;width:100%;height:46px;
        background:linear-gradient(90deg,var(--band-green),var(--band-lime));
        display:flex;align-items:center;justify-content:center;
        font-family:"Cinzel",serif;font-weight:700;color:var(--ink);letter-spacing:2px}
  .card--back .band{top:302px;font-size:26px}
  .card--front .band{top:232px;font-size:21px}

  .locations{position:absolute;left:30px;top:376px;color:var(--text-light)}
  .locations__title{font-family:"Cinzel",serif;font-weight:700;font-size:19px;letter-spacing:1px;margin-bottom:16px}
  .locations__list{list-style:none}
  .locations__item{display:flex;align-items:center;font-size:18px;margin-bottom:12px}
  .locations__box{width:15px;height:15px;border:1.5px solid var(--text-light);margin-right:14px;flex:none}

  .badge{position:absolute;left:148px;top:138px;width:84px;height:70px;border-radius:10px;background:var(--badge-orange)}

  .contact-icons{position:absolute;top:318px;left:0;width:100%;display:flex;justify-content:center;gap:22px}
  .contact-icon{width:40px;height:40px;border-radius:50%;background:var(--icon-lime);display:flex;align-items:center;justify-content:center}
  .contact-icon svg{width:22px;height:22px}

  .contact{position:absolute;top:390px;left:0;width:100%;text-align:center;color:var(--text-light)}
  .contact__phone{font-family:"Cinzel",serif;font-weight:700;font-size:25px;letter-spacing:1px;line-height:1.45}
  .contact__line{font-size:17px;line-height:1.6}
  .contact__email{margin-top:22px}
</style>
</head>
<body>

<section class="card card--back" aria-label="Appointment card">
  <div class="appt-sheet">
    <p class="brand-name">Brightfield Nutrition &amp; Dietetics</p>
    <ul class="appt-fields">
      <li class="appt-field">Date:<span class="appt-field__line"></span></li>
      <li class="appt-field">Time:<span class="appt-field__line"></span></li>
      <li class="appt-field">Date:<span class="appt-field__line"></span></li>
      <li class="appt-field">Time:<span class="appt-field__line"></span></li>
    </ul>
  </div>
  <div class="band">APPOINTMENT</div>
  <div class="locations">
    <h2 class="locations__title">APPOINTMENT LOCATION</h2>
    <ul class="locations__list">
      <li class="locations__item"><span class="locations__box"></span>North Corrin Health</li>
      <li class="locations__item"><span class="locations__box"></span>Hollis Medical</li>
      <li class="locations__item"><span class="locations__box"></span>Pinebrook Medical Centre</li>
      <li class="locations__item"><span class="locations__box"></span>Ashcombe Doctors Surgery</li>
    </ul>
  </div>
</section>

<section class="card card--front" aria-label="Business card front">
  <p class="brand-name">Brightfield Nutrition &amp; Dietetics</p>
  <div class="badge" role="img" aria-label="Accreditation badge"></div>
  <div class="band">MARCUS KELLERMAN</div>

  <div class="contact-icons">
    <span class="contact-icon" aria-label="Fax">
      <svg viewBox="0 0 24 24" fill="none" stroke="#2a2c2d" stroke-width="1.8"><rect x="5" y="3" width="14" height="8"/><rect x="3" y="11" width="18" height="8" rx="1"/><line x1="7" y1="15" x2="13" y2="15"/></svg>
    </span>
    <span class="contact-icon" aria-label="Phone">
      <svg viewBox="0 0 24 24" fill="#2a2c2d"><path d="M6.6 10.8a15 15 0 0 0 6.6 6.6l2.2-2.2a1 1 0 0 1 1-.25 11.4 11.4 0 0 0 3.6.57 1 1 0 0 1 1 1V20a1 1 0 0 1-1 1A17 17 0 0 1 3 4a1 1 0 0 1 1-1h3.5a1 1 0 0 1 1 1c0 1.25.2 2.45.57 3.6a1 1 0 0 1-.25 1z"/></svg>
    </span>
    <span class="contact-icon" aria-label="Email">
      <svg viewBox="0 0 24 24" fill="none" stroke="#2a2c2d" stroke-width="1.8"><rect x="3" y="6" width="18" height="13" rx="1"/><polyline points="3,6 12,13 21,6"/></svg>
    </span>
    <span class="contact-icon" aria-label="Website">
      <svg viewBox="0 0 24 24" fill="none" stroke="#2a2c2d" stroke-width="1.8"><circle cx="12" cy="12" r="9"/><ellipse cx="12" cy="12" rx="4" ry="9"/><line x1="3" y1="12" x2="21" y2="12"/></svg>
    </span>
  </div>

  <div class="contact">
    <p class="contact__phone">6457 2183</p>
    <p class="contact__phone">0427 561 903</p>
    <p class="contact__line contact__email">marcus.k.diet@fernmail.com</p>
    <p class="contact__line">www.brightfieldnutrition.com.au</p>
  </div>
</section>

</body>
</html>
```